Investor Slide Deck

Simple idea - take a model investor deck and build out a investor deck for K7V. I will complete the data, I need a template to work from within. I will attach a model investor deck and a blank K7V that I need built out to K7V. Use the K7V Pwrpt to build out the investor deck

```html
<!DOCTYPE html>
<html lang="en">
<head>
<meta charset="utf-8">
<title>K7V Investor Deck 2024</title>
<link href="https://fonts.googleapis.com/css2?family=Montserrat:wght@400;500;600;700;800&family=Lato:ital,wght@0,400;0,700;1,700&display=swap" rel="stylesheet">
<style>
:root{
  --board:#8c8c8c;
  --paper:#f7f7f7;
  --ink:#1e1e1e;
  --muted:#3c3c3c;
  --blue:#1452a6;
  --teal:#4abdb2;
  --deep-teal:#1b6784;
  --orange:#f2561b;
  --yellow:#f5c33b;
  --white:#ffffff;
}
*{box-sizing:border-box;margin:0;padding:0}
html,body{width:1007px;height:1200px;overflow:hidden;background:var(--board)}
body{font-family:'Lato',sans-serif;color:var(--ink)}
.board{position:relative;width:1007px;height:1200px}
.slide{position:absolute;width:439px;height:247px;background:var(--paper);overflow:hidden}
.s1{left:48px;top:47px}.s2{left:524px;top:47px}
.s3{left:48px;top:331px}.s4{left:524px;top:331px}
.s5{left:50px;top:616px}.s6{left:524px;top:616px}
.s7{left:50px;top:901px}.s8{left:524px;top:901px}
.abs{position:absolute}
.accent-bars{position:absolute;left:22px;top:5px;display:flex;gap:4px}
.accent-bars span{display:block;height:2px;border-radius:1px;background:var(--teal);width:29px}
.accent-bars span+span{background:var(--deep-teal);width:18px}
.slide-title{position:absolute;left:21px;top:11px;font-family:'Montserrat',sans-serif;font-weight:700;font-size:14px;letter-spacing:.2px;color:var(--ink)}
.brand{position:absolute;right:22px;top:6px;display:flex;align-items:center;gap:3px;font-family:'Montserrat',sans-serif;font-weight:600;font-size:5px;color:var(--ink)}
.brand i{display:block;width:8px;height:8px;border-radius:50%;background:var(--orange)}
.footer-note{position:absolute;left:22px;bottom:7px;font-family:'Lato',sans-serif;font-style:italic;font-weight:700;font-size:5.2px}
.page-no{position:absolute;right:22px;bottom:7px;font-family:'Lato',sans-serif;font-weight:700;font-size:5.2px}
.page-no b{color:var(--teal);font-size:7px}
.base-band{position:absolute;left:0;right:0;bottom:0;height:2px;background:var(--teal)}
.base-band::after{content:"";position:absolute;right:0;top:0;width:94px;height:2px;background:var(--deep-teal)}

/* cover */
.cover{background:var(--blue)}
.cover-title{right:22px;top:125px;text-align:right;font-family:'Montserrat',sans-serif;font-weight:800;font-size:21px;color:var(--white)}
.cover-sub{right:22px;top:152px;text-align:right;font-family:'Montserrat',sans-serif;font-size:8.5px;line-height:13.5px;color:var(--white)}
.cover-pill{right:22px;top:186px;background:var(--white);color:var(--blue);border-radius:10px;padding:5px 8px;font-family:'Montserrat',sans-serif;font-weight:700;font-size:7px}
.cover-brand{right:22px;top:215px;display:flex;align-items:center;gap:5px;font-family:'Montserrat',sans-serif;font-weight:600;font-size:12px;color:var(--white)}
.cover-brand i{display:block;width:22px;height:22px;border-radius:50%;background:var(--white)}

/* problems */
.intro{left:22px;top:31px;width:400px;font-size:5.2px;line-height:10px;color:var(--muted)}
.hub{left:163px;top:53px;width:113px;height:24px;border-radius:12px;background:var(--white);box-shadow:0 1px 4px rgba(0,0,0,.12);display:flex;align-items:center;justify-content:center;gap:3px;font-family:'Montserrat',sans-serif;font-weight:600;font-size:6px}
.hub i{display:block;width:11px;height:11px;border-radius:50%;background:var(--orange)}
.issue{position:absolute;top:162px;width:72px;margin-left:-36px;text-align:center}
.issue h4{font-family:'Lato',sans-serif;font-weight:700;font-size:4.4px;line-height:8.5px;min-height:17px}
.issue p{font-size:3.8px;line-height:8.8px;color:var(--muted)}

/* services */
.service{position:absolute;top:80px;width:124px;height:133px;border:1.5px solid var(--teal);border-top:none}
.service::before,.service::after{content:"";position:absolute;top:0;width:16px;border-top:1.5px solid var(--teal)}
.service::before{left:-1.5px}.service::after{right:-1.5px}
.service.yellow,.service.yellow::before,.service.yellow::after{border-color:var(--yellow)}
.service-photo{position:absolute;top:-44px;left:17px;width:90px;height:90px;border-radius:50%;border:1.5px solid var(--teal)}
.service.yellow .service-photo{border-color:var(--yellow)}
.service h3{position:absolute;left:10px;top:62px;font-family:'Montserrat',sans-serif;font-weight:600;font-size:8px}
.service ul{position:absolute;left:10px;top:78px;list-style:none}
.service li{position:relative;padding-left:7px;font-size:5px;line-height:11px;color:var(--muted)}
.service li::before{content:"";position:absolute;left:0;top:4px;width:3.5px;height:3.5px;border-radius:50%;background:var(--teal)}
.service.yellow li::before{background:var(--yellow)}

/* advantage */
.adv-icon{position:absolute;width:54px;height:54px;border-radius:50%;display:flex;align-items:center;justify-content:center}
.adv{position:absolute;width:124px;margin-left:-62px;text-align:center}
.adv h3{font-family:'Montserrat',sans-serif;font-weight:600;font-size:8.5px;margin-bottom:6px}
.adv p{font-size:6px;line-height:12.5px;color:var(--muted)}

/* team */
.member{position:absolute;top:43px;width:110px;height:169px;border:1px solid var(--teal);border-radius:55px;text-align:center}
.member.orange{border-color:var(--orange)}.member.deep{border-color:var(--deep-teal)}
.member-photo{position:absolute;left:16px;top:6px;width:78px;height:78px;border-radius:50%;border-bottom:1.5px solid var(--teal)}
.member.orange .member-photo{border-color:var(--orange)}.member.deep .member-photo{border-color:var(--deep-teal)}
.member h3{position:absolute;left:0;right:0;top:92px;font-family:'Montserrat',sans-serif;font-weight:600;font-size:7.8px;color:var(--teal)}
.member.orange h3{color:var(--orange)}.member.deep h3{color:var(--deep-teal)}
.member p{position:absolute;left:11px;right:11px;top:106px;font-size:3.7px;line-height:8.2px;color:var(--muted)}

/* fund raise */
.raise-sub{left:22px;top:37px;font-family:'Montserrat',sans-serif;font-weight:700;font-size:8.5px;color:var(--teal)}
.raise-text{left:22px;top:54px;width:170px;font-size:5.3px;line-height:11px;color:var(--muted)}
.raise-text b{color:var(--ink)}
.legend{position:absolute;display:flex;align-items:center;gap:7px;font-family:'Montserrat',sans-serif;font-weight:600;font-size:6.8px}
.legend i{display:block;width:25px;height:25px;border-radius:50%}

/* phases */
.phase-tag{position:absolute;left:23px;width:19px;height:62px;display:flex;align-items:center;justify-content:center}
.phase-tag span{transform:rotate(-90deg);white-space:nowrap;font-family:'Montserrat',sans-serif;font-weight:800;font-size:8px}
.phase-head{position:absolute;left:50px;font-family:'Montserrat',sans-serif;font-weight:700;font-size:8.5px;line-height:14px}
.metric{position:absolute;padding-left:9px;font-family:'Montserrat',sans-serif;font-weight:600;font-size:6.3px;line-height:11.5px}
.metric::before{content:"";position:absolute;left:0;top:4px;width:1.5px;height:24px;background:currentColor}
.metric::after{content:"";position:absolute;left:-1px;top:2px;width:3.5px;height:3.5px;border-radius:50%;background:currentColor}
.metric.y{color:var(--yellow)}.metric.b{color:var(--blue)}
.metric span{color:var(--ink)}

/* thank you */
.end-brand{left:22px;top:35px;display:flex;align-items:center;gap:5px;font-family:'Montserrat',sans-serif;font-weight:600;font-size:12.5px}
.end-brand i{display:block;width:22px;height:22px;border-radius:50%;background:var(--orange)}
.thanks{left:21px;top:75px;font-family:'Montserrat',sans-serif;font-weight:800;font-size:20px}
.contact-head{left:22px;top:108px;font-family:'Montserrat',sans-serif;font-weight:500;font-size:11px}
.contact{position:absolute;left:22px;display:flex;align-items:flex-start;gap:7px;font-family:'Montserrat',sans-serif;font-weight:500;font-size:8.2px;line-height:13.5px}
.contact i{flex:none;width:18px;height:18px;border-radius:50%;background:var(--teal);display:flex;align-items:center;justify-content:center}
</style>
</head>
<body>
<main class="board">

  <!-- 1 cover -->
  <section class="slide s1 cover">
    <svg class="abs" style="left:0;top:0" width="439" height="247" viewBox="0 0 439 247">
      <defs>
        <linearGradient id="coverScene" x1="0" y1="0" x2="1" y2="1">
          <stop offset="0" stop-color="#b9c9bd"/>
          <stop offset=".45" stop-color="#8f9c8a"/>
          <stop offset="1" stop-color="#5d6a66"/>
        </linearGradient>
      </defs>
      <polygon role="img" aria-label="Family standing with solar panels in front of a house with a solar roof" points="0,0 439,0 439,20 170,222 0,222" fill="url(#coverScene)"/>
      <g fill="var(--blue)">
        <polygon points="0,128 160,0 180,0 0,145"/>
        <polygon points="0,182 232,0 252,0 0,196"/>
        <polygon points="30,222 312,0 332,0 58,222"/>
        <polygon points="95,222 380,0 400,0 120,222"/>
      </g>
    </svg>
    <h1 class="abs cover-title">WE'RE K7V</h1>
    <p class="abs cover-sub">When education becomes relevant,<br>learners fully engage.</p>
    <div class="abs cover-pill">INVESTOR DECK, 2024</div>
    <div class="abs cover-brand"><i></i>KELVARA POWER</div>
  </section>

  <!-- 2 problems -->
  <section class="slide s2">
    <div class="accent-bars"><span></span><span></span></div>
    <h2 class="slide-title">PROBLEMS</h2>
    <div class="brand"><i></i>KELVARA POWER</div>
    <p class="abs intro">Every year, the rise in prices of electricity is burning a hole in the pocket of consumers. <b>Solar Power</b> is a reliable solution, but the industry is facing its own set of challenges.</p>
    <svg class="abs" style="left:0;top:0" width="439" height="247" viewBox="0 0 439 247" fill="none" stroke="#9a9a9a" stroke-width=".6" stroke-dasharray="1.5 1.5">
      <path d="M176,77 V100 H56.6 V126"/>
      <path d="M196,77 V114 H137.8 V126"/>
      <path d="M219,77 V126"/>
      <path d="M242,77 V110 H300 V126"/>
      <path d="M262,77 V97 H382 V126"/>
      <g stroke-dasharray="none">
        <circle cx="56.6" cy="142" r="14.5" stroke="var(--deep-teal)" stroke-width="3.5" fill="#fff"/>
        <circle cx="137.8" cy="142" r="14.5" stroke="var(--orange)" stroke-width="3.5" fill="#fff"/>
        <circle cx="219" cy="142" r="14.5" stroke="var(--yellow)" stroke-width="3.5" fill="#fff"/>
        <circle cx="300" cy="142" r="14.5" stroke="var(--teal)" stroke-width="3.5" fill="#fff"/>
        <circle cx="382" cy="142" r="14.5" stroke="var(--ink)" stroke-width="3.5" fill="#fff"/>
        <circle cx="56.6" cy="142" r="6" stroke="var(--deep-teal)" stroke-width="1"/>
        <circle cx="56.6" cy="142" r="2" stroke="var(--deep-teal)" stroke-width="1"/>
        <circle cx="137.8" cy="142" r="6" stroke="var(--orange)" stroke-width="1"/>
        <path d="M134.8,142 l2,2 l4,-4" stroke="var(--orange)" stroke-width="1"/>
        <rect x="213" y="137" width="12" height="9" rx="1" stroke="var(--yellow)" stroke-width="1"/>
        <path d="M216,141 h6" stroke="var(--yellow)" stroke-width="1"/>
        <circle cx="300" cy="142" r="6" stroke="var(--teal)" stroke-width="1"/>
        <path d="M297,142 h6 M300,139 v6" stroke="var(--teal)" stroke-width="1"/>
        <rect x="377" y="136" width="9" height="11" rx="1" stroke="var(--ink)" stroke-width="1"/>
        <circle cx="386" cy="145" r="3" stroke="var(--ink)" stroke-width="1"/>
      </g>
    </svg>
    <div class="abs hub"><i></i>KELVARA POWER</div>
    <div class="issue" style="left:56.6px"><h4>Poor Quality<br>Components</h4><p>The use of low-quality solar panels and components in solar plant construction is impacting their efficiency and lifespan.</p></div>
    <div class="issue" style="left:137.8px"><h4>Poor Installation</h4><p>Solar plant installations demand precision; poor installation can lead to downtime, damage, and efficiency loss.</p></div>
    <div class="issue" style="left:219px"><h4>Lack of Awareness</h4><p>Limited awareness of government subsidies and inadequate financing options for high-cost solar plant purchases can lead to missed product benefits</p></div>
    <div class="issue" style="left:300px"><h4>Unreliable Customer<br>and Warranty Support</h4><p>Challenges in reaching timely support and clarifying warranty terms can result in customer frustration and issue resolution.</p></div>
    <div class="issue" style="left:382px"><h4>Lack of Transparency in<br>Pricing and Performance</h4><p>Customers might encounter unexpected hidden costs during installation &amp; lower energy generation than agreed upon</p></div>
    <div class="footer-note">Private &amp; Confidential | 2024</div>
    <div class="page-no">Page Number: <b>2</b></div>
    <div class="base-band"></div>
  </section>

  <!-- 3 services -->
  <section class="slide s3">
    <div class="accent-bars" style="left:38px"><span></span><span></span></div>
    <h2 class="slide-title">OUR SERVICES</h2>
    <div class="brand"><i></i>KELVARA POWER</div>
    <div class="service" style="left:22px">
      <div class="service-photo" role="img" aria-label="House roof covered with solar panels at sunset" style="background:linear-gradient(180deg,#d9a468,#5d6578 55%,#3c4750)"></div>
      <h3>Solar Power for Homes</h3>
      <ul><li>Electricity Bill to go to Zero</li><li>Low Maintenance Cost</li><li>Assured Warranty upto 25 Years</li><li>Government Subsidies</li></ul>
    </div>
    <div class="service yellow" style="left:157px">
      <div class="service-photo" role="img" aria-label="Solar panel array with a wind turbine under blue sky" style="background:linear-gradient(180deg,#4d8fd6,#a9cdf0 45%,#2c4c86 70%,#6d9a3a)"></div>
      <h3>Solar Power for Business</h3>
      <ul><li>Clean Energy</li><li>Tax Benefits</li><li>Grid Tied Systems</li><li>Finance Support</li></ul>
    </div>
    <div class="service" style="left:292px">
      <div class="service-photo" role="img" aria-label="Two engineers walking between rows of a utility solar farm" style="background:linear-gradient(180deg,#b7d6ee,#4c6a8e 40%,#6f8a55 80%)"></div>
      <h3>Utility Scale Solar Power</h3>
      <ul><li>Generate and Sell electricity to the<br>government and industrial plants</li><li>Long term stable prices for generated<br>electricity from solar power plant</li></ul>
    </div>
    <div class="footer-note">Private &amp; Confidential | 2024</div>
    <div class="page-no">Page Number: <b>3</b></div>
    <div class="base-band"></div>
  </section>

  <!-- 4 advantage -->
  <section class="slide s4">
    <div class="accent-bars"><span></span><span></span></div>
    <h2 class="slide-title" style="top:13px">COMPETITIVE ADVANTAGE</h2>
    <div class="brand"><i></i>KELVARA POWER</div>
    <div class="adv-icon" style="left:48.5px;top:51px;background:var(--orange)">
      <svg width="26" height="26" viewBox="0 0 26 26" fill="none" stroke="#fff" stroke-width="1.2"><circle cx="13" cy="9" r="6"/><path d="M10.5,9 l2,2 l3.5,-4"/><path d="M3,14 v6 l6,4 M23,14 v6 l-6,4"/></svg>
    </div>
    <div class="adv-icon" style="left:189.6px;top:78.7px;background:var(--deep-teal)">
      <svg width="26" height="26" viewBox="0 0 26 26" fill="none" stroke="#fff" stroke-width="1.2"><circle cx="13" cy="11" r="6"/><path d="M10,17 v3 h6 v-3"/><circle cx="5" cy="6" r="3"/><circle cx="21" cy="19" r="3"/></svg>
    </div>
    <div class="adv-icon" style="left:331.4px;top:51px;background:var(--yellow)">
      <svg width="26" height="26" viewBox="0 0 26 26" fill="none" stroke="#fff" stroke-width="1.2"><circle cx="13" cy="13" r="3"/><circle cx="6" cy="15" r="2.5"/><circle cx="20" cy="15" r="2.5"/><path d="M4,23 c2,-6 16,-6 18,0"/><path d="M13,3 l1,2 h2 l-1.5,1.5 l.5,2 l-2,-1 l-2,1 l.5,-2 l-1.5,-1.5 h2z"/></svg>
    </div>
    <div class="adv" style="left:75.5px;top:116px"><h3>Focus on Quality</h3><p>Our stringent quality control methods enable us to provide high-quality products that we provide <b>warranties upto 25 years.</b></p></div>
    <div class="adv" style="left:216.6px;top:144px"><h3>State of the Art Technology</h3><p>Our access to advanced technology lets us create cutting-edge solar solutions that adapt flexibly to suit specific requirements.</p></div>
    <div class="adv" style="left:358.4px;top:116px"><h3>Unrivalled Experience</h3><p>We have worked on <b>2500+ projects</b> maintaining consistent quality. Experience and Technology enable us to provide best results for our customers.</p></div>
    <div class="footer-note">Private &amp; Confidential | 2024</div>
    <div class="page-no">Page Number: <b>4</b></div>
    <div class="base-band"></div>
  </section>

  <!-- 5 team -->
  <section class="slide s5">
    <div class="accent-bars"><span></span><span></span></div>
    <h2 class="slide-title">MANAGEMENT TEAM</h2>
    <div class="brand"><i></i>KELVARA POWER</div>
    <div class="member" style="left:32px">
      <div class="member-photo" role="img" aria-label="Portrait of the chief executive in a dark suit" style="background:linear-gradient(180deg,#c9d3dc,#2d3a4d)"></div>
      <h3>CEO - Marcus Hale</h3>
      <p>Lorem ipsum dolor sit amet, consectetur adipiscing elit, sed do eiusmod tempor incididunt ut labore et dolore magna aliqua. Ut enim ad minim veniam, quis nostrud exercitation ullamco laboris nisi ut aliquip ex ea commodo consequat.</p>
    </div>
    <div class="member orange" style="left:163.5px">
      <div class="member-photo" role="img" aria-label="Portrait of the chief technology officer in a blazer" style="background:linear-gradient(180deg,#e3e6e8,#3b3d42)"></div>
      <h3>CTO- Dorian Lenk</h3>
      <p>Lorem ipsum dolor sit amet, consectetur adipiscing elit, sed do eiusmod tempor incididunt ut labore et dolore magna aliqua. Ut enim ad minim veniam, quis nostrud exercitation ullamco laboris nisi ut aliquip ex ea commodo consequat.</p>
    </div>
    <div class="member deep" style="left:296px">
      <div class="member-photo" role="img" aria-label="Portrait of the chief executive in a grey suit" style="background:linear-gradient(180deg,#e4e4e4,#4a5560)"></div>
      <h3>CEO - Marcus Hale</h3>
      <p>Lorem ipsum dolor sit amet, consectetur adipiscing elit, sed do eiusmod tempor incididunt ut labore et dolore magna aliqua. Ut enim ad minim veniam, quis nostrud exercitation ullamco laboris nisi ut aliquip ex ea commodo consequat.</p>
    </div>
    <div class="footer-note">Private &amp; Confidential | 2024</div>
    <div class="page-no">Page Number: <b>5</b></div>
    <div class="base-band"></div>
  </section>

  <!-- 6 fund raise chart -->
  <section class="slide s6">
    <div class="accent-bars"><span></span><span></span></div>
    <h2 class="slide-title">FUND RAISE</h2>
    <div class="brand"><i></i>KELVARA POWER</div>
    <p class="abs raise-sub">Company Name Energy is raising:</p>
    <p class="abs raise-text">Total Funding – <b>₹122Cr INR ($14.5 Mn)</b> to build and start operations of a solar panel manufacturing plant in India.<br><br>We are looking to raise capital in a 65% Equity and 35% Debt ratio.</p>
    <div class="legend" style="left:22px;top:121px"><i style="background:var(--deep-teal)"></i>Working Capital</div>
    <div class="legend" style="left:122px;top:121px"><i style="background:var(--teal)"></i>CAPEX</div>
    <div class="legend" style="left:22px;top:157px"><i style="background:var(--orange)"></i>Payroll</div>
    <div class="legend" style="left:122px;top:157px"><i style="background:var(--yellow)"></i>Startup Expenses</div>
    <svg class="abs" style="left:244px;top:48px" width="160" height="160" viewBox="0 0 160 160">
      <circle cx="80" cy="80.6" r="78" fill="#eeeeee"/>
      <g transform="rotate(-90 80 80.6)" fill="none" stroke-width="46">
        <circle cx="80" cy="80.6" r="51" pathLength="100" stroke="var(--teal)" stroke-dasharray="38 62"/>
        <circle cx="80" cy="80.6" r="51" pathLength="100" stroke="var(--deep-teal)" stroke-dasharray="58 42" stroke-dashoffset="-38"/>
        <circle cx="80" cy="80.6" r="51" pathLength="100" stroke="var(--yellow)" stroke-dasharray="2 98" stroke-dashoffset="-96"/>
        <circle cx="80" cy="80.6" r="51" pathLength="100" stroke="var(--orange)" stroke-dasharray="2 98" stroke-dashoffset="-98"/>
      </g>
      <circle cx="80" cy="80.6" r="28" fill="#fff"/>
      <text x="80" y="85" text-anchor="middle" font-family="Montserrat, sans-serif" font-weight="600" font-size="13" fill="var(--teal)">K7V</text>
      <g font-family="Montserrat, sans-serif" font-weight="700" font-size="9" fill="#fff" text-anchor="middle">
        <text x="122" y="62">38%</text>
        <text x="35" y="106">58%</text>
      </g>
    </svg>
    <div class="footer-note">Private &amp; Confidential | 2024</div>
    <div class="page-no">Page Number: <b>6</b></div>
    <div class="base-band"></div>
  </section>

  <!-- 7 fund raise phases -->
  <section class="slide s7">
    <div class="accent-bars"><span></span><span></span></div>
    <h2 class="slide-title">FUND RAISE</h2>
    <div class="brand"><i></i>KELVARA POWER</div>
    <div class="phase-tag" style="top:51px;background:var(--yellow)"><span>PHASE I</span></div>
    <div class="phase-tag" style="top:129px;background:var(--blue);color:#fff"><span>PHASE II</span></div>
    <div class="phase-head" style="top:70px">FIRST AND SECOND<br>YEAR OF OPERATIONS:</div>
    <div class="metric y" style="left:164px;top:72px"><span>120MW OF SOLAR<br>PROJECTS –₹480CR</span></div>
    <div class="metric y" style="left:250px;top:67px"><span>120MW OF SOLAR<br>PANEL SALES -<br>₹240CR</span></div>
    <div class="metric y" style="left:332px;top:72px"><span>TARGET REVENUE BY<br>2ND YEAR - ₹720CR</span></div>
    <div class="phase-head" style="top:148px">SECOND TO FOURTH<br>YEAR OF OPERATIONS:</div>
    <div class="metric b" style="left:164px;top:150px"><span>240MW OF SOLAR<br>PROJECTS –₹960CR</span></div>
    <div class="metric b" style="left:250px;top:145px"><span>240MW OF SOLAR<br>PANEL SALES -<br>₹480CR</span></div>
    <div class="metric b" style="left:332px;top:150px"><span>TARGET REVENUE BY<br>4TH YEAR - ₹1440CR</span></div>
    <div class="footer-note">Private &amp; Confidential | 2024</div>
    <div class="page-no">Page Number: <b>7</b></div>
    <div class="base-band"></div>
  </section>

  <!-- 8 thank you -->
  <section class="slide s8">
    <div class="abs end-brand"><i></i>KELVARA POWER</div>
    <h2 class="abs thanks">THANK YOU!</h2>
    <p class="abs contact-head">CONTACT US</p>
    <div class="contact" style="top:135px"><i><svg width="9" height="9" viewBox="0 0 10 10" fill="#fff"><path d="M2,1 l2,0 l1,2.5 l-1.3,1 a5,5 0 0 0 1.8,1.8 l1,-1.3 l2.5,1 l0,2 a1,1 0 0 1 -1,1 a8,8 0 0 1 -7,-7 a1,1 0 0 1 1,-1z"/></svg></i><span>PHONE:&nbsp; +1 555 014 7788</span></div>
    <div class="contact" style="top:164px"><i><svg width="9" height="9" viewBox="0 0 10 10" fill="none" stroke="#fff" stroke-width="1"><rect x="1" y="2" width="8" height="6" rx=".5"/><path d="M1,2.5 l4,3 l4,-3"/></svg></i><span>EMAIL:&nbsp; INFO@KELVARAPOWER</span></div>
    <div class="contact" style="top:188px"><i style="margin-top:6px"><svg width="9" height="9" viewBox="0 0 10 10" fill="#fff"><path d="M5,0.5 a3.5,3.5 0 0 1 3.5,3.5 c0,2.5 -3.5,5.5 -3.5,5.5 c0,0 -3.5,-3 -3.5,-5.5 a3.5,3.5 0 0 1 3.5,-3.5z"/><circle cx="5" cy="4" r="1.2" fill="var(--teal)"/></svg></i><span>ADDRESS:&nbsp; KELVARA POWER,<br>UNITED STATE.</span></div>
    <svg class="abs" style="left:224px;top:29px" width="192" height="192" viewBox="0 0 192 192">
      <circle cx="96" cy="96" r="92" fill="none" stroke="var(--teal)" stroke-width="6"/>
      <defs><linearGradient id="workerScene" x1="0" y1="0" x2="0" y2="1"><stop offset="0" stop-color="#b8d4ea"/><stop offset=".45" stop-color="#8a9a8c"/><stop offset="1" stop-color="#3a4f6e"/></linearGradient></defs>
      <circle role="img" aria-label="Smiling solar technician in a hard hat standing in front of solar panels" cx="96" cy="96" r="85" fill="url(#workerScene)"/>
    </svg>
    <div class="base-band" style="background:transparent"></div>
  </section>

</main>
</body>
</html>
```